1876 Basins & Spouts Business Card

I'm wanting to get a business card designed. Our business is 1876 Basins & Spouts
Details for the card:

1876 Basins & Spouts
Name: Harold Vesk
Email: harold@1876basinsandspouts.com.au
Website: www.1876basinsandspouts.com.au
Mobile: 0438 260 947
Phone: 02 7481 3926

Font of Basins & Spouts is called Snell Roundhand. Not sue what font logo text is.

I'm thinking two sided but it doesn't have to be.

```html
<!DOCTYPE html>
<html lang="en">
<head>
<meta charset="utf-8">
<title>1876 Basins &amp; Spouts Business Card</title>
<link rel="stylesheet" href="https://fonts.googleapis.com/css2?family=Cormorant+Garamond:wght@500&family=Roboto:wght@400;700&display=swap">
<style>
  :root {
    --backdrop: #2c2c2e;
    --card: #ffffff;
    --ink: #1a1a1a;
    --ink-soft: #444444;
    --rule: #cfcfcf;
  }
  * { margin: 0; padding: 0; box-sizing: border-box; }
  html, body { width: 1200px; height: 840px; overflow: hidden; }
  body {
    background: var(--backdrop);
    display: flex;
    align-items: center;
    justify-content: center;
    gap: 60px;
    font-family: "Roboto", Arial, sans-serif;
    color: var(--ink);
  }
  .card {
    position: relative;
    width: 520px;
    height: 300px;
    background: var(--card);
    box-shadow: 0 6px 0 #0e0e0e, 0 18px 40px rgba(0,0,0,.45);
    overflow: hidden;
  }

  /* Front side */
  .card-front .brand {
    position: absolute;
    left: 70px; top: 92px;
    display: flex; align-items: center; gap: 18px;
  }
  .brand-dot {
    width: 64px; height: 64px;
    border: 2px solid var(--ink);
    border-radius: 50%;
    flex: none;
  }
  .brand-name {
    font-family: "Cormorant Garamond", Georgia, serif;
    font-weight: 500;
    font-size: 34px;
    color: var(--ink);
    line-height: 1;
    white-space: nowrap;
  }
  .brand-tagline {
    margin-top: 8px;
    font-size: 9.5px;
    letter-spacing: .3px;
    color: var(--ink-soft);
    white-space: nowrap;
  }
  .card-front .front-web {
    position: absolute;
    left: 0; right: 0; top: 214px;
    text-align: center;
    font-size: 14px;
    letter-spacing: 2.6px;
    color: var(--ink);
  }

  /* Back side */
  .card-back .back-mark {
    position: absolute;
    left: 22px; top: 116px;
    width: 232px;
    display: flex; align-items: center; gap: 10px;
  }
  .card-back .brand-dot { width: 40px; height: 40px; border-width: 1.5px; }
  .card-back .brand-name { font-size: 21px; }
  .divider {
    position: absolute;
    left: 262px; top: 70px;
    width: 1px; height: 160px;
    background: var(--rule);
    box-shadow: 2px 0 6px rgba(0,0,0,.12);
  }
  .contact {
    position: absolute;
    left: 282px; top: 86px;
  }
  .contact-name {
    font-weight: 700;
    font-size: 21px;
    margin-bottom: 12px;
  }
  .contact-list { list-style: none; }
  .contact-list li {
    display: flex; align-items: center; gap: 8px;
    font-size: 11.5px;
    line-height: 19px;
    color: var(--ink);
    white-space: nowrap;
  }
  .contact-list svg { width: 11px; height: 11px; flex: none; }
</style>
</head>
<body>

  <section class="card card-front" aria-label="Card front">
    <div class="brand">
      <span class="brand-dot"></span>
      <div>
        <div class="brand-name">1876 Basins &amp; Spouts</div>
        <div class="brand-tagline">Heritage craftsmanship shaped for everyday living</div>
      </div>
    </div>
    <div class="front-web">www.1876basinsandspouts.com.au</div>
  </section>

  <section class="card card-back" aria-label="Card back">
    <div class="back-mark">
      <span class="brand-dot"></span>
      <span class="brand-name">1876 Basins &amp; Spouts</span>
    </div>
    <div class="divider"></div>
    <div class="contact">
      <div class="contact-name">Harold Vesk</div>
      <ul class="contact-list">
        <li>
          <svg viewBox="0 0 12 12" aria-hidden="true"><path d="M2.5 1 L4.5 1 L5.2 3.6 L4 4.6 Q5 6.8 7.4 8 L8.4 6.8 L11 7.5 L11 9.5 Q10.5 11 9 11 Q1 10 1 3 Q1 1.5 2.5 1Z" fill="#1a1a1a"/></svg>
          02 7481 3926
        </li>
        <li>
          <svg viewBox="0 0 12 12" aria-hidden="true"><rect x="2.5" y="0.8" width="7" height="10.4" rx="1.2" fill="none" stroke="#1a1a1a" stroke-width="1.2"/><circle cx="6" cy="9.4" r=".7" fill="#1a1a1a"/></svg>
          0438 260 947
        </li>
        <li>
          <svg viewBox="0 0 12 12" aria-hidden="true"><rect x="0.8" y="2.2" width="10.4" height="7.6" fill="none" stroke="#1a1a1a" stroke-width="1.2"/><path d="M1 2.6 L6 6.6 L11 2.6" fill="none" stroke="#1a1a1a" stroke-width="1.2"/></svg>
          harold@1876basinsandspouts.com.au
        </li>
        <li>
          <svg viewBox="0 0 12 12" aria-hidden="true"><circle cx="6" cy="6" r="5.2" fill="#1a1a1a"/><path d="M1 6 H11 M6 1 Q3 6 6 11 M6 1 Q9 6 6 11" fill="none" stroke="#fff" stroke-width=".8"/></svg>
          www.1876basinsandspouts.com.au
        </li>
      </ul>
    </div>
  </section>

</body>
</html>
```